Förderverein einer Kirchengemeinde sucht Flyer-Design
Zielgruppe
Wir sind ein Förderverein einer Kirchengemeinde, der sich für die kirchenmusikalische Arbeit einsetzt.
Wir wünschen uns ein niveauvolles und zeitgemäßes/modernes Flyerdesign, das die etablierten Konzertbesucher anspricht, aber vor allem auch Menschen erreicht und überzeugt, die (noch) nichts mit Kirche zu tun haben.
Das Alter der (Haupt-) Zielgruppe (Männer und Frauen) erstreckt sich von 45 bis 70 Jahren.
Aufgabenstellung
Bei der Wahl des Formates würden wir (aus der Sicht von Laien) ein zweimal gefaltetes DIN A4 quer Format nehmen. Aber wir lassen uns gerne überraschen und sind grundsätzlich für andere Lösungen offen.
Bitte den Abschnitt für Adress- und sonstige Dateneintragungen samt Kontodaten so gestalten und platzieren, dass man ihn leicht abtrennen und verschicken kann.
Der Flyer soll Kirchenmusik als lebendig und attraktiv darstellen und neue (jüngere) Mitglieder für den Freundeskreis werben.
Lassen Sie die Bilder sprechen!!

```html
<!DOCTYPE html>
<html lang="de">
<head>
<meta charset="utf-8">
<title>Beitrittserklärung – Förderkreis Musica Sacra</title>
<link rel="stylesheet" href="https://fonts.googleapis.com/css2?family=Source+Sans+3:ital,wght@0,400;0,600;0,700;1,400&display=swap">
<style>
  :root {
    --red: #c0161c;
    --ink: #333333;
    --label: #555555;
    --rule: #bdbdbd;
    --band: #d9d9d9;
    --paper: #ffffff;
  }
  * { box-sizing: border-box; margin: 0; padding: 0; }
  html, body { width: 1200px; height: 848px; overflow: hidden; background: var(--paper); }
  body { font-family: "Source Sans 3", sans-serif; color: var(--ink); position: relative; }
  .abs { position: absolute; }

  .form-side { position: absolute; left: 0; top: 0; width: 719px; height: 848px; background: var(--paper); }
  .title { left: 37px; top: 24px; font-size: 28px; font-weight: 600; color: var(--red); }

  .grid { left: 35px; width: 656px; border: 1.5px solid var(--rule); }
  .hline { position: absolute; left: 0; right: 0; height: 0; border-top: 1.5px solid var(--rule); }
  .vline { position: absolute; width: 0; border-left: 1.5px solid var(--rule); }
  .write-line { position: absolute; height: 0; border-top: 1px solid #888; }
  .label { position: absolute; font-size: 14.5px; color: var(--label); }

  .band { left: 35px; width: 656px; height: 32px; background: var(--band); font-size: 17.5px; font-weight: 600; color: #444; padding: 5px 0 0 8px; }

  .check { position: absolute; font-size: 15.5px; color: #444; display: flex; align-items: center; gap: 5px; letter-spacing: 0.2px; }
  .check::before { content: ""; width: 13px; height: 13px; border: 1.3px solid #666; display: inline-block; }
  .note { position: absolute; font-size: 13.5px; font-style: italic; color: #444; }

  .account { left: 37px; top: 725px; font-size: 17.5px; color: #444; font-weight: 600; }
  .account-lines { left: 176px; top: 727px; font-size: 13.5px; color: #444; line-height: 22.5px; }

  .cut { left: 716px; top: 0; width: 0; height: 848px; border-left: 2px dashed #555; }
  .cut-text { position: absolute; left: 702px; top: 822px; transform-origin: left top; transform: rotate(-90deg); font-size: 8.5px; color: #666; white-space: nowrap; }
  .scissors { position: absolute; left: 705px; top: 738px; width: 14px; height: 14px; }

  .info-side { position: absolute; left: 726px; top: 0; width: 474px; height: 848px; background: var(--red); color: #fff; }
  .organ-photo { position: absolute; left: 0; top: 0; width: 474px; height: 423px;
    background: linear-gradient(180deg, #d9d6cf 0%, #c9b27a 18%, #b8a9a0 40%, #a85a55 60%, #b9b9b6 80%, #d8d4cc 100%); }
  .brand { position: absolute; top: 462px; left: 52px; display: flex; align-items: center; gap: 12px; font-size: 21px; font-weight: 600; }
  .brand-dot { width: 18px; height: 18px; border-radius: 50%; background: #fff; }
  .intro { position: absolute; left: 52px; top: 518px; font-size: 18px; line-height: 22.5px; }
  .intro b { font-weight: 700; }
  .address { position: absolute; left: 103px; top: 623px; font-size: 19.5px; font-weight: 700; line-height: 24.2px; }
  .more { position: absolute; left: 52px; top: 756px; font-size: 18px; line-height: 26px; }
  .more b { font-weight: 700; }
</style>
</head>
<body>
  <section class="form-side">
    <h1 class="abs title">Beitrittserklärung</h1>

    <div class="abs grid" style="top:69px;height:213px;">
      <div class="hline" style="top:31px"></div>
      <div class="hline" style="top:62px"></div>
      <div class="hline" style="top:122px"></div>
      <div class="hline" style="top:153px"></div>
      <div class="vline" style="left:323px;top:122px;height:90px"></div>
      <div class="write-line" style="left:7px;width:643px;top:93px"></div>
      <div class="write-line" style="left:7px;width:301px;top:202px"></div>
      <div class="write-line" style="left:333px;width:314px;top:203px"></div>
      <span class="label" style="left:7px;top:6px">Name, Vorname</span>
      <span class="label" style="left:7px;top:37px">für die Institution/Firma + persönlich</span>
      <span class="label" style="left:7px;top:67px">Straße, Hausnr., PLZ, Ort</span>
      <span class="label" style="left:7px;top:128px">Telefon/Handy</span>
      <span class="label" style="left:333px;top:128px">Geburtstag</span>
      <span class="label" style="left:7px;top:158px">Emailadresse</span>
      <span class="label" style="left:333px;top:158px">Datum, Unterschrift</span>
    </div>

    <div class="abs band" style="top:306px">Mitgliedsbeiträge</div>
    <span class="check" style="left:38px;top:348px">Einzelpersonen € 20,-</span>
    <span class="check" style="left:38px;top:372px">Ehepaare/Partnerschaften € 32,-</span>
    <span class="check" style="left:38px;top:396px">Institutionen/Firmen € 95,-</span>
    <span class="note" style="left:56px;top:422px">(jeweils Mindestbeiträge)</span>
    <span class="check" style="left:350px;top:348px">&nbsp;Frei wählbarer Betrag : €</span>
    <div class="write-line" style="left:544px;width:146px;top:370px;border-color:#999"></div>
    <span class="check" style="left:350px;top:378px">&nbsp;Ich benötige eine Spendenbescheinigung</span>
    <span class="check" style="left:350px;top:408px">&nbsp;Einmalige Spende <i>&nbsp;(ohne Mitgliedschaft)</i></span>

    <div class="abs grid" style="top:464px;height:248px;">
      <div class="hline" style="top:30px"></div>
      <div class="hline" style="top:70px"></div>
      <div class="hline" style="top:113px"></div>
      <div class="hline" style="top:211px"></div>
      <div class="vline" style="left:391px;top:30px;height:40px"></div>
      <div class="vline" style="left:322px;top:70px;height:43px"></div>
      <div class="write-line" style="left:199px;width:440px;top:198px;border-color:#999"></div>
      <span class="label" style="left:7px;top:40px">IBAN</span>
      <span class="label" style="left:398px;top:40px">BIC</span>
      <span class="label" style="left:7px;top:81px">Kreditinstitut</span>
      <span class="label" style="left:329px;top:81px">Kontoinhaber</span>
      <span class="label" style="left:7px;top:124px;line-height:18px;width:620px">Hiermit ermächtige ich den Förderkreis Musica Sacra den von mir zu entrichtenden Mitgliedsbeitrag von meinem Konto einzuziehen</span>
      <span class="label" style="left:7px;top:179px">Ort, Datum, Unterschrift</span>
      <span class="label" style="left:7px;top:219px;font-style:italic;font-size:13.5px">Der Einzug der Mitgliedsbeiträge erfolgt zu Beginn eines Kalenderjahres</span>
    </div>
    <div class="abs band" style="top:464px;height:30px;padding-top:4px;">SEPA-Lastschriftmandat</div>

    <div class="abs account">Spendenkonto:</div>
    <div class="abs account-lines">
      Sparkasse Lindenfeld<br>
      IBAN: DE 0012 3456 7890 1234 5678<br>
      BIC: SPKLDE21XXX<br>
      Verwendungszweck bei Einzelspenden unter Angabe der Kostenstelle …
    </div>

    <svg class="scissors" viewBox="0 0 14 14" aria-hidden="true">
      <circle cx="4" cy="11" r="2.2" fill="none" stroke="#666" stroke-width="1"/>
      <circle cx="10" cy="11" r="2.2" fill="none" stroke="#666" stroke-width="1"/>
      <path d="M5.5 9.5 L11 1 M8.5 9.5 L3 1" stroke="#666" stroke-width="1" fill="none"/>
    </svg>
    <span class="cut-text">Hier abtrennen</span>
  </section>

  <div class="abs cut"></div>

  <section class="info-side">
    <div class="organ-photo" role="img" aria-label="Foto der barocken Orgel mit goldverzierten Türmen und silbernen Pfeifen"></div>
    <div class="brand"><span class="brand-dot"></span><span>Förderkreis Musica Sacra</span></div>
    <p class="intro">Wenn Sie die Kirchenmusik an St. Albertus<br>als Mitglied im <b>Förderkreis Musica Sacra</b><br>fördern möchten, senden Sie die ausgefüllte<br>Beitrittserklärung an den</p>
    <p class="address">Förderkreis Musica Sacra,<br>Kirchengemeinde St. Albertus,<br>Kirchgasse 7, 38999 Lindenfeld,<br>Tel.: 05399-204718,<br>m.hollert@kirche-lindenfeld.de</p>
    <p class="more">Nähere Informationen finden Sie unter<br><b>www.kirchenmusik-lindenfeld.de</b></p>
  </section>
</body>
</html>
```